Redesign of business card for Cedar Ridge Mechanical

We are looking for a new design for our business cards for Cedar Ridge Mechanical. We are a plumbing & HVAC construction company, operating on the West Coast of Canada and USA. Logo attached.
Industry/Entity Type
Construction - Plumbing & HVAC
Contact Information for Business Card
Name, address, phone numbers, email, website address
Look and feel
Each slider illustrates characteristics of the customer's brand and the style your logo design should communicate.

```html
<!DOCTYPE html>
<html lang="en">
<head>
<meta charset="utf-8">
<title>Cedar Ridge Mechanical – Business Card</title>
<link rel="stylesheet" href="https://fonts.googleapis.com/css2?family=Open+Sans:wght@400;700&display=swap">
<style>
  :root {
    --bg: #d9d9d9;
    --card: #ffffff;
    --ink: #000000;
    --text-muted: #555555;
    --text-body: #222222;
    --swoosh-grey: #9a9a9a;
  }
  html, body {
    margin: 0;
    padding: 0;
    width: 1200px;
    height: 896px;
    overflow: hidden;
    background: var(--bg);
    font-family: "Open Sans", sans-serif;
  }
  .canvas {
    position: relative;
    width: 1200px;
    height: 896px;
  }
  .card {
    position: absolute;
    left: 334px;
    width: 528px;
    height: 300px;
    background: var(--card);
    border-radius: 24px;
    overflow: hidden;
  }
  .card--front { top: 126px; }
  .card--back { top: 475px; height: 301px; }

  .brand {
    position: absolute;
    display: flex;
    align-items: center;
    color: var(--ink);
    font-weight: 700;
    text-transform: uppercase;
    white-space: nowrap;
  }
  .brand__square {
    background: var(--ink);
    flex: none;
  }
  .card--front .brand {
    left: 0;
    right: 0;
    top: 120px;
    justify-content: center;
    font-size: 27px;
    letter-spacing: 1px;
    gap: 14px;
  }
  .card--front .brand__square { width: 26px; height: 26px; }

  .card--back .brand {
    left: 44px;
    top: 106px;
    font-size: 14px;
    gap: 8px;
  }
  .card--back .brand__square { width: 14px; height: 14px; }

  .divider {
    position: absolute;
    left: 281px;
    top: 67px;
    width: 1.5px;
    height: 167px;
    background: var(--ink);
  }
  .contact {
    position: absolute;
    left: 300px;
    top: 63px;
    color: var(--text-body);
  }
  .contact__name {
    margin: 0;
    font-size: 19px;
    font-weight: 700;
    line-height: 1.2;
    color: var(--ink);
  }
  .contact__title {
    margin: 0 0 10px;
    font-size: 14px;
    line-height: 1.3;
    color: var(--text-muted);
  }
  .contact__address {
    margin: 0 0 8px;
    font-size: 14px;
    line-height: 19px;
    color: var(--text-muted);
    font-style: normal;
  }
  .contact__list {
    list-style: none;
    margin: 0;
    padding: 0;
    font-size: 14px;
    line-height: 19px;
  }
  .contact__list li {
    display: flex;
    align-items: center;
    gap: 6px;
  }
  .contact__list svg {
    width: 11px;
    height: 11px;
    flex: none;
  }
  .swoosh {
    position: absolute;
    left: 0;
    top: 0;
    width: 528px;
    height: 301px;
  }
</style>
</head>
<body>
<main class="canvas">

  <section class="card card--front" aria-label="Card front">
    <div class="brand">
      <span class="brand__square"></span>
      <span>Cedar Ridge Mechanical</span>
    </div>
  </section>

  <section class="card card--back" aria-label="Card back">
    <svg class="swoosh" viewBox="0 0 528 301" aria-hidden="true">
      <path d="M0,237 Q250,305 528,256 L528,301 L0,301 Z" fill="var(--ink)"/>
      <path d="M105,262 Q330,290 528,244 L528,254 Q330,298 105,262 Z" fill="var(--swoosh-grey)"/>
      <path d="M80,266 Q330,300 528,254 L528,259 Q330,304 80,266 Z" fill="var(--card)"/>
    </svg>

    <div class="brand">
      <span class="brand__square"></span>
      <span>Cedar Ridge Mechanical</span>
    </div>

    <div class="divider"></div>

    <div class="contact">
      <h1 class="contact__name">DANIEL REYES</h1>
      <p class="contact__title">Managing Director</p>
      <address class="contact__address">Your address, City<br>State, Zip 1234</address>
      <ul class="contact__list">
        <li>
          <svg viewBox="0 0 12 12"><path d="M2.5,1 L4.5,1 L5.2,3.5 L4,4.5 Q5,7 7.5,8 L8.5,6.8 L11,7.5 L11,9.5 Q10.5,11 9,11 Q1,10 1,2.5 Q1,1 2.5,1 Z" fill="var(--ink)"/></svg>
          <span>123 456 789</span>
        </li>
        <li>
          <svg viewBox="0 0 12 12"><rect x="3" y="0.5" width="6" height="11" rx="1" fill="none" stroke="var(--ink)" stroke-width="1.3"/><rect x="5" y="9.3" width="2" height="1" fill="var(--ink)"/></svg>
          <span>123 456 789</span>
        </li>
        <li>
          <svg viewBox="0 0 12 12"><rect x="0.7" y="3" width="10.6" height="8" fill="none" stroke="var(--ink)" stroke-width="1.2"/><path d="M0.7,3 L6,7.5 L11.3,3" fill="none" stroke="var(--ink)" stroke-width="1.2"/></svg>
          <span>info@yourgmail.com</span>
        </li>
        <li>
          <svg viewBox="0 0 12 12"><circle cx="6" cy="6" r="5.3" fill="var(--ink)"/><path d="M3,4 Q5,3 5,5 Q7,6 6,8 M8,2.5 Q9,5 10.5,5" fill="none" stroke="var(--card)" stroke-width="1"/></svg>
          <span>www.yourwebsite.com</span>
        </li>
      </ul>
    </div>
  </section>

</main>
</body>
</html>
```